Local Roofing/Construction company business needs new biz card design

We need a new business card design, current cards are from the start of this operation and generic at best. We are a local Construction Company (General Contractor) with a majority of our work originating from insurance claims-exterior finish work is the main focus (Roofs-Siding-Gutters etc). Heavily involved with homeowners and the low ball offers they receive from insurance company's after a insurable event takes place. I have attached some of our original logo file(s) below.

```html
<!DOCTYPE html>
<html lang="en">
<head>
<meta charset="utf-8">
<title>Norcrest Construction – Business Card</title>
<link rel="stylesheet" href="https://fonts.googleapis.com/css2?family=Poppins:wght@400;600&display=swap">
<style>
  :root {
    --backdrop: #2b2b2b;
    --card-white: #ffffff;
    --brand-green: #33d97a;
    --brand-dark: #0e1f20;
    --ink: #1b1b1b;
    --divider: #cfcfcf;
  }
  * { box-sizing: border-box; margin: 0; padding: 0; }
  html, body {
    width: 1093px; height: 1200px; overflow: hidden;
    background: var(--backdrop);
    font-family: "Poppins", sans-serif;
  }
  .canvas { position: relative; width: 1093px; height: 1200px; }

  .card {
    position: absolute; left: 265px; width: 579px; height: 356px;
    border-radius: 24px;
  }
  .card--front { top: 226px; background: var(--card-white); }
  .card--back  { top: 621px; background: var(--brand-green); }

  /* Front: brand block */
  .brand-block {
    position: absolute; left: 63px; top: 81px; width: 192px; height: 195px;
    display: flex; flex-direction: column; justify-content: center; align-items: center;
    gap: 14px;
  }
  .brand-square {
    width: 86px; height: 86px; background: var(--brand-green); border-radius: 4px;
  }
  .brand-name {
    font-weight: 600; color: var(--brand-green);
    font-size: 19px; line-height: 1.15; text-align: center; letter-spacing: 0.5px;
  }

  .divider {
    position: absolute; left: 289px; top: 74px; width: 1px; height: 209px;
    background: var(--divider);
  }

  .contact { position: absolute; left: 311px; top: 90px; color: var(--ink); }
  .contact__name {
    font-weight: 600; font-size: 21px; line-height: 1; color: var(--brand-green);
    letter-spacing: 0.3px;
  }
  .contact__title { font-size: 16.5px; line-height: 1.2; margin-top: 2px; }
  .contact__list { list-style: none; margin-top: 12px; }
  .contact__item {
    display: flex; align-items: center; gap: 7px;
    font-size: 17px; line-height: 21px;
  }
  .contact__item svg { width: 16px; height: 16px; flex: none; }
  .accent { color: var(--brand-green); }
  .contact__address { font-size: 16.5px; line-height: 21px; margin-top: 12px; }

  /* Back */
  .back-mark {
    position: absolute; inset: 0;
    display: flex; align-items: center; justify-content: center; gap: 16px;
  }
  .back-square { width: 40px; height: 40px; background: var(--brand-dark); border-radius: 4px; }
  .back-name {
    font-weight: 600; font-size: 30px; color: var(--brand-dark); letter-spacing: 1px;
  }
</style>
</head>
<body>
<main class="canvas">
  <section class="card card--front" aria-label="Business card front">
    <div class="brand-block">
      <span class="brand-square" aria-hidden="true"></span>
      <p class="brand-name">NORCREST<br>CONSTRUCTION</p>
    </div>
    <div class="divider"></div>
    <div class="contact">
      <h1 class="contact__name">DANIEL MERCER</h1>
      <p class="contact__title">Managing Director</p>
      <ul class="contact__list">
        <li class="contact__item">
          <svg viewBox="0 0 24 24" aria-hidden="true"><path fill="#33d97a" d="M6.6 10.8a15.1 15.1 0 0 0 6.6 6.6l2.2-2.2c.3-.3.7-.4 1-.2 1.1.4 2.3.6 3.6.6.6 0 1 .4 1 1V20c0 .6-.4 1-1 1A17 17 0 0 1 3 4c0-.6.4-1 1-1h3.5c.6 0 1 .4 1 1 0 1.3.2 2.5.6 3.6.1.3 0 .7-.2 1z"/></svg>
          055-218 640 317
        </li>
        <li class="contact__item">
          <svg viewBox="0 0 24 24" aria-hidden="true"><path fill="#33d97a" d="M2 5h20v14H2z"/><path fill="none" stroke="#fff" stroke-width="1.6" d="M2 5l10 8 10-8M2 19l7-7M22 19l-7-7"/></svg>
          hello@norcrestbuild.com
        </li>
        <li class="contact__item">
          <svg viewBox="0 0 24 24" aria-hidden="true"><g fill="none" stroke="#33d97a" stroke-width="1.8"><circle cx="12" cy="12" r="9.5"/><ellipse cx="12" cy="12" rx="4" ry="9.5"/><path d="M2.5 12h19M4 7h16M4 17h16"/></g></svg>
          www.<span class="accent">norcrestbuild</span>.com
        </li>
      </ul>
      <p class="contact__address">218, Harlow Ridge Road<br>60417, Westbrook</p>
    </div>
  </section>

  <section class="card card--back" aria-label="Business card back">
    <div class="back-mark">
      <span class="back-square" aria-hidden="true"></span>
      <p class="back-name">NORCREST CONSTRUCTION</p>
    </div>
  </section>
</main>
</body>
</html>
```